AUTOMOTIVE/ CAR REPAIRS / CRASH REPAIRS / PAINT SPRAYING AND PANEL BEATING

AUTOMOTIVE REPAIR. CAR / MOTORCYCLES GOT LOGO DESIGN / DID THINK ABOUT FACEBOOK DONT NOALREADY HAVE WEB ADRESS www.brenvashine.co.uk and mail sales@brenvashine,co.uk NEED SOMETHINK I CAN MANAGE TO UPLOAD PICTURES IN TO A GALLERY OR SOMETHINGLIKE THAT I ALSO SELL CAR AND MOTORCYCLES MAYBE A SELLS PAGE WITH A TILLWAVE LINK

Target Market(s)

TRADE / GENERAL PUBLIC

Industry/Entity Type

Automotive

Coding

Coded - Design and coding required

Number of Pages Required

4 page

Font styles to use
Serif
Sans Serif

Colors

Designer to choose colors to be used in the design.

Requirements
Must have
• GALLERY/ SHOP TO SALE CARS AND MOTORCYCLE / LOGOS OF MATERIALS I USE DORFLINT / KEBO / VASTINCO / Q WRAP / GLENBRUSH
• CONTACT US
Nice to have
• TILLWAVE / EASY TO MANAGE / VIDEO CLIP OF DORFLINT HUE PLANNER Z7
• SWIFT BLEND PAINT TONVIEW WETLINE AND TULVOKE

```html
<!DOCTYPE html>
<html lang="en">
<head>
<meta charset="utf-8">
<title>Brenvashine Bodyshop</title>
<link href="https://fonts.googleapis.com/css2?family=Lato:wght@700;900&family=Roboto:wght@400;500;700&display=swap" rel="stylesheet">
<style>
:root{
  --maroon:#6e1f2c;
  --maroon-dark:#3a0f17;
  --ink:#111111;
  --text:#555555;
  --white:#ffffff;
  --grey-band:#ececec;
  --footer:#121212;
  --star:#f5a623;
}
*{margin:0;padding:0;box-sizing:border-box}
html,body{width:1200px;height:4376px;overflow:hidden;background:var(--white)}
body{position:relative;font-family:'Roboto',sans-serif;color:var(--text)}
.abs{position:absolute}
.heading{font-family:'Lato',sans-serif;font-weight:900;color:var(--ink);font-size:40px;letter-spacing:.5px}
.center{left:0;width:1200px;text-align:center}
.btn{position:absolute;background:var(--maroon);color:var(--white);font:700 16px 'Roboto',sans-serif;display:flex;align-items:center;justify-content:center;gap:10px}
.btn svg{width:16px;height:16px}

/* header + hero */
.hero{left:0;top:0;width:1200px;height:527px;background:linear-gradient(90deg,#5a5252 0%,#8a8585 35%,#6b3a3a 60%,#a01820 78%,#3c3c3c 100%)}
.topbar{left:0;top:0;width:1200px;height:66px;background:rgba(20,20,20,.85)}
.brand{left:118px;top:14px;color:var(--white);font:900 22px 'Lato',sans-serif;letter-spacing:2px}
.brand small{display:block;font:500 10px 'Roboto',sans-serif;letter-spacing:6px;text-align:center;margin-top:-2px}
.nav{left:392px;top:22px;display:flex;gap:25px;color:var(--white);font:700 16px 'Roboto',sans-serif}
.nav .active{border-bottom:3px solid var(--white);padding-bottom:7px}
.login{left:1000px;top:17px;width:85px;height:34px}
.hero-title{left:112px;top:186px;color:var(--white);font:900 56px 'Lato',sans-serif}
.hero-text{left:112px;top:270px;color:var(--white);font-size:17px;line-height:27px;width:440px}

/* about */
.about-img{left:110px;top:655px;width:477px;height:263px;background:radial-gradient(ellipse at center,#8c7b66 0%,#b9ab99 45%,#ffffff 72%)}
.about-title{left:660px;top:646px}
.about-text{left:660px;top:712px;width:440px;font-size:16.5px;line-height:26px}
.rule{left:105px;top:990px;width:976px;height:1px;background:#cccccc}

/* services */
.ring{left:413px;top:1241px;width:374px;height:374px;border-radius:50%;background:#e3e3e3}
.ring-photo{left:455px;top:1283px;width:290px;height:290px;border-radius:50%;background:radial-gradient(circle at 50% 45%,#f2f2f2 0%,#c9c9c9 45%,#3a3a3a 100%)}
.badge{width:74px;height:74px;border-radius:50%;background:var(--white);box-shadow:0 3px 10px rgba(0,0,0,.2);display:flex;align-items:center;justify-content:center}
.badge svg{width:38px;height:38px}
.svc h4{font:700 16px 'Roboto',sans-serif;color:var(--ink);margin-bottom:8px}
.svc p{font-size:15px;line-height:26px;color:#777}
.svc.right{text-align:right}

/* custom */
.custom{left:0;top:1751px;width:1200px;height:337px;background:linear-gradient(180deg,#efefef,#e2e2e2)}
.custom-text{top:1885px;font-size:17px;line-height:27px;color:#222}

/* gallery */
.grid{left:114px;top:2276px;width:974px;display:grid;grid-template-columns:repeat(4,240px);grid-auto-rows:197px;gap:5px}
.tile{width:240px;height:197px}
.partners{left:110px;top:2760px;width:980px;display:flex;justify-content:space-around;align-items:center}
.partner{font:700 24px 'Roboto',sans-serif;color:#222;display:flex;align-items:center;gap:8px}
.partner i{width:18px;height:18px;border-radius:50%;background:#222;display:inline-block}

/* appointment */
.appt{left:0;top:2880px;width:1200px;height:460px;background:var(--maroon)}
.appt .heading{color:var(--white)}
.appt-addr{top:2998px;color:var(--white);font:700 18px 'Roboto',sans-serif;line-height:27px}
.field{position:absolute;background:var(--white);display:flex;align-items:center;gap:14px;padding-left:22px;font-size:16px;color:#444}
.field svg{width:16px;height:16px}
.appt-note{top:3258px;color:var(--white);font-size:17px}

/* testimonials */
.card{width:478px;height:350px;background:var(--white);box-shadow:0 2px 8px rgba(0,0,0,.25)}
.card-top{position:absolute;left:0;top:0;width:478px;height:197px;background:linear-gradient(135deg,var(--maroon) 0%,var(--maroon-dark) 60%,#1a1a1a 100%)}
.quote{position:absolute;color:var(--white);font:900 70px 'Lato',sans-serif;line-height:1}
.card-text{position:absolute;left:70px;top:70px;width:350px;color:var(--white);font-size:16.5px;line-height:26px;text-align:justify}
.avatar{position:absolute;left:193px;top:151px;width:92px;height:92px;border-radius:50%;border:4px solid var(--white);background:linear-gradient(180deg,#d8d2cc,#8c8580)}
.stars{position:absolute;left:0;top:265px;width:478px;display:flex;justify-content:center;gap:9px}
.stars svg{width:22px;height:22px}
.name{position:absolute;left:0;top:300px;width:478px;text-align:center;font:700 20px 'Roboto',sans-serif;color:var(--ink)}
.name span{font-weight:400;color:#555}

/* footer */
.footer{left:0;top:3995px;width:1200px;height:381px;background:var(--footer)}
.foot-h{font:700 17px 'Roboto',sans-serif;color:var(--white);text-decoration:underline}
.links{list-style:none;color:var(--white);font-size:16px}
.links li{height:39px;display:flex;align-items:center;gap:10px}
.contact-row{display:flex;align-items:center;gap:22px;color:var(--white);font-size:16.5px;line-height:27px}
.contact-row i{width:34px;height:34px;border-radius:50%;background:var(--white);display:flex;align-items:center;justify-content:center;flex:none}
.contact-row svg{width:18px;height:18px}
.map{left:731px;top:4071px;width:357px;height:198px;background:linear-gradient(135deg,#e5efd9,#cfe1bd 50%,#f1eee6)}
.directions{left:745px;top:4083px;background:var(--white);padding:8px 12px;font:700 14px 'Roboto',sans-serif;color:#222;box-shadow:0 1px 3px rgba(0,0,0,.3);display:flex;gap:8px;align-items:center}
.foot-rule{left:110px;top:4318px;width:978px;height:1px;background:#555}
.social{left:123px;top:4336px;display:flex;gap:26px}
.social i{width:18px;height:18px;border-radius:50%;background:var(--white);display:block}
.copy{top:4336px;color:var(--white);font-size:16px}
.pay{left:1010px;top:4334px;color:var(--white);font:700 18px 'Roboto',sans-serif}
</style>
</head>
<body>

<!-- hero -->
<div class="abs hero" role="img" aria-label="Red sports car on a misty road"></div>
<div class="abs topbar"></div>
<div class="abs brand">BRENVASHINE<small>BODYSHOP</small></div>
<nav class="abs nav"><span class="active">HOME</span><span>ABOUT US</span><span>SERVICE</span><span>CUSTOM</span><span>GALLERY</span><span>CONTACT</span></nav>
<div class="btn login">LOGIN</div>
<h1 class="abs hero-title">BRENVASHINE</h1>
<p class="abs hero-text">Brenvashine, based in Ashcombe, Holmshire established in August, 1985 has grown to become Holmshire's.</p>
<div class="btn" style="left:112px;top:354px;width:155px;height:39px">
<svg viewBox="0 0 16 16" fill="#fff"><path d="M1 2h2.5l2 8h8l1.5-6H5" stroke="#fff" stroke-width="1.6" fill="none"/><circle cx="6.5" cy="13" r="1.4"/><circle cx="12.5" cy="13" r="1.4"/></svg>SHOP NOW</div>

<!-- about -->
<div class="abs about-img" role="img" aria-label="Bronze saloon car"></div>
<h2 class="abs heading about-title">ABOUT US</h2>
<p class="abs about-text">Equipped with the latest technology and factory trained technicians, we process accident repairs for all leading insurance and vehicle management companies, specialising in accident repairs for most prestige vehicles manufacturers. We are proud to maintain a close working partnership with several local dealership networks,.</p>
<div class="btn" style="left:660px;top:887px;width:161px;height:41px">READ MORE
<svg viewBox="0 0 16 16"><circle cx="8" cy="8" r="7.5" fill="#fff"/><path d="M6 4.5 9.5 8 6 11.5" stroke="#6e1f2c" stroke-width="2" fill="none"/></svg></div>
<div class="abs rule"></div>

<!-- services -->
<h2 class="abs heading center" style="top:1044px">OUR SERVICES</h2>
<div class="abs ring"></div>
<div class="abs ring-photo" role="img" aria-label="White car in a workshop"></div>
<div class="abs badge" style="left:561px;top:1230px"><svg viewBox="0 0 24 24" fill="none" stroke="#222" stroke-width="1.6"><path d="M4 8h10v5H4zM14 10h4M7 13v6h3v-6"/></svg></div>
<div class="abs badge" style="left:402px;top:1330px"><svg viewBox="0 0 24 24" fill="none" stroke="#222" stroke-width="1.6"><rect x="4" y="6" width="16" height="12" rx="2"/><path d="M8 12h8"/></svg></div>
<div class="abs badge" style="left:716px;top:1330px"><svg viewBox="0 0 24 24" fill="#222"><path d="M5 19l5-5 3 3-5 5zM12 12l6-8 2 2-8 6z"/></svg></div>
<div class="abs badge" style="left:448px;top:1513px"><svg viewBox="0 0 24 24" fill="none" stroke="#222" stroke-width="1.6"><path d="M3 15l2-5h12l3 5v3H3z"/><circle cx="7" cy="18" r="2"/><circle cx="17" cy="18" r="2"/></svg></div>
<div class="abs badge" style="left:674px;top:1520px"><svg viewBox="0 0 24 24" fill="none" stroke="#222" stroke-width="1.6"><circle cx="8" cy="6" r="2.5"/><path d="M8 9v7l-3 5M12 13h8v5h-8z"/></svg></div>

<div class="abs svc" style="left:505px;top:1137px"><h4>FULL OR PART RESPRAYS</h4><p>Single panel resprays to fullcar resprays<br>Single panel resprays.</p></div>
<div class="abs svc right" style="left:72px;top:1329px;width:300px"><h4>REPAIRED &amp; PAINTED</h4><p>The cost of alloy wheel repair or wheel refurbishment is far lower.</p></div>
<div class="abs svc" style="left:813px;top:1330px;width:290px"><h4>DENTS &amp; SCRATCH REMOVAL</h4><p>The techniques used are methods that enable professionals to repair.</p></div>
<div class="abs svc right" style="left:122px;top:1538px;width:300px"><h4>ACCIDENT REPAIR</h4><p>Sometimes accidents happen which result in you needing your vehicle.</p></div>
<div class="abs svc" style="left:777px;top:1553px;width:290px"><h4>BUMPER REPAIR</h4><p>Car bumper scuff damage can not only harm the appearance.</p></div>

<!-- custom -->
<div class="abs custom"></div>
<h2 class="abs heading center" style="top:1818px">CUSTOM</h2>
<p class="abs center custom-text">Our experienced team can efficiently carry out any customising work you require in<br>order to meet the specific design you have in mind.</p>
<div class="btn" style="left:519px;top:1972px;width:161px;height:39px">READ MORE
<svg viewBox="0 0 16 16"><circle cx="8" cy="8" r="7.5" fill="#fff"/><path d="M6 4.5 9.5 8 6 11.5" stroke="#6e1f2c" stroke-width="2" fill="none"/></svg></div>

<!-- gallery -->
<h2 class="abs heading center" style="top:2164px">GALLERY</h2>
<div class="abs grid">
  <div class="tile" role="img" aria-label="Car body in pink primer" style="background:linear-gradient(135deg,#b9a3ad,#d9b7c9 50%,#7d6a70)"></div>
  <div class="tile" role="img" aria-label="Red car shell in workshop" style="background:linear-gradient(135deg,#d8d8d8,#c8231f 50%,#7a1010)"></div>
  <div class="tile" role="img" aria-label="Covered car in spray booth" style="background:linear-gradient(135deg,#6a6a6a,#b5b5b5 50%,#3a3a3a)"></div>
  <div class="tile" role="img" aria-label="Classic car body stripped" style="background:linear-gradient(135deg,#8a7f6c,#cbc4aa 50%,#4c463a)"></div>
  <div class="tile" role="img" aria-label="Glossy black panel" style="background:linear-gradient(135deg,#3a3020,#151515 50%,#6b5a3a)"></div>
  <div class="tile" role="img" aria-label="Silver alloy wheel" style="background:radial-gradient(circle,#e5e5e5,#9a9a9a 55%,#2a2a2a)"></div>
  <div class="tile" role="img" aria-label="Red motorcycle in garage" style="background:linear-gradient(135deg,#4e5a6a,#c0262a 55%,#2a2a2a)"></div>
  <div class="tile" role="img" aria-label="Car interior with white leather" style="background:linear-gradient(135deg,#2a2a2a,#d9d9d9 55%,#555)"></div>
</div>
<div class="abs partners">
  <span class="partner">DORFLINT</span>
  <span class="partner">KEBO</span>
  <span class="partner"><i></i>VASTINCO</span>
  <span class="partner">Q WRAP</span>
  <span class="partner">GLENBRUSH</span>
</div>

<!-- appointment -->
<div class="abs appt"></div>
<h2 class="abs heading center" style="top:2928px;color:#fff">APPOINTMENT</h2>
<p class="abs center appt-addr">BRENVASHINE BODY SHOP , LARKFIELD BUSINESS PARK<br>FERN LANE , ASHCOMBE , HOLMSHIRE , HS 12 7 QR</p>
<div class="field" style="left:173px;top:3089px;width:431px;height:61px">
<svg viewBox="0 0 16 16" fill="none" stroke="#666" stroke-width="1.4"><rect x="1.5" y="3" width="13" height="11.5"/><path d="M1.5 6.5h13M5 1v3M11 1v3"/></svg>Date</div>
<div class="field" style="left:615px;top:3089px;width:417px;height:61px">
<svg viewBox="0 0 16 16" fill="none" stroke="#666" stroke-width="1.4"><circle cx="8" cy="8" r="6.5"/><path d="M8 4v4h3"/></svg>Time</div>
<div class="field" style="left:170px;top:3162px;width:865px;height:61px"><span style="width:16px">$</span>Price</div>
<p class="abs center appt-note">If you are unable to keep your appointment , please contact us as soon as possible.</p>

<!-- testimonials -->
<h2 class="abs heading center" style="top:3428px">TESTIMONIALS</h2>
<div class="abs card" style="left:110px;top:3531px">
  <div class="card-top"></div>
  <span class="quote" style="left:18px;top:14px">“</span>
  <p class="card-text">Lorem ipsum dolor sit amet, consectetur adipiscing elit, sed do eiusmod tempor incididunt ut labore et dolore.</p>
  <span class="quote" style="left:410px;top:130px">”</span>
  <div class="avatar" role="img" aria-label="Customer portrait"></div>
  <div class="stars"><svg viewBox="0 0 24 24"><path fill="#f5a623" d="M12 2l3 7 7 .6-5.3 4.7 1.6 7.2L12 17.8 5.7 21.5l1.6-7.2L2 9.6 9 9z"/></svg><svg viewBox="0 0 24 24"><path fill="#f5a623" d="M12 2l3 7 7 .6-5.3 4.7 1.6 7.2L12 17.8 5.7 21.5l1.6-7.2L2 9.6 9 9z"/></svg><svg viewBox="0 0 24 24"><path fill="#f5a623" d="M12 2l3 7 7 .6-5.3 4.7 1.6 7.2L12 17.8 5.7 21.5l1.6-7.2L2 9.6 9 9z"/></svg><svg viewBox="0 0 24 24"><path fill="#f5a623" d="M12 2l3 7 7 .6-5.3 4.7 1.6 7.2L12 17.8 5.7 21.5l1.6-7.2L2 9.6 9 9z"/></svg><svg viewBox="0 0 24 24"><path fill="#f5a623" d="M12 2l3 7 7 .6-5.3 4.7 1.6 7.2L12 17.8 5.7 21.5l1.6-7.2L2 9.6 9 9z"/></svg></div>
  <p class="name">TOMAS ARDEN , <span>Customer</span></p>
</div>
<div class="abs card" style="left:612px;top:3531px">
  <div class="card-top"></div>
  <span class="quote" style="left:18px;top:14px">“</span>
  <p class="card-text">Lorem ipsum dolor sit amet, consectetur adipiscing elit, sed do eiusmod tempor incididunt ut labore et dolore.</p>
  <span class="quote" style="left:410px;top:130px">”</span>
  <div class="avatar" role="img" aria-label="Customer portrait"></div>
  <div class="stars"><svg viewBox="0 0 24 24"><path fill="#f5a623" d="M12 2l3 7 7 .6-5.3 4.7 1.6 7.2L12 17.8 5.7 21.5l1.6-7.2L2 9.6 9 9z"/></svg><svg viewBox="0 0 24 24"><path fill="#f5a623" d="M12 2l3 7 7 .6-5.3 4.7 1.6 7.2L12 17.8 5.7 21.5l1.6-7.2L2 9.6 9 9z"/></svg><svg viewBox="0 0 24 24"><path fill="#f5a623" d="M12 2l3 7 7 .6-5.3 4.7 1.6 7.2L12 17.8 5.7 21.5l1.6-7.2L2 9.6 9 9z"/></svg><svg viewBox="0 0 24 24"><path fill="#f5a623" d="M12 2l3 7 7 .6-5.3 4.7 1.6 7.2L12 17.8 5.7 21.5l1.6-7.2L2 9.6 9 9z"/></svg><svg viewBox="0 0 24 24"><path fill="#f5a623" d="M12 2l3 7 7 .6-5.3 4.7 1.6 7.2L12 17.8 5.7 21.5l1.6-7.2L2 9.6 9 9z"/></svg></div>
  <p class="name">OWEN HARTLEY , <span>Customer</span></p>
</div>

<!-- footer -->
<div class="abs footer"></div>
<h3 class="abs foot-h" style="left:117px;top:4063px">QUICK LINKS</h3>
<ul class="abs links" style="left:117px;top:4093px">
  <li>» Home</li><li>» About Us</li><li>» Services</li><li>» Gallery</li><li>» Contact Us</li>
</ul>
<h3 class="abs foot-h" style="left:366px;top:4063px">CONTACT US</h3>
<div class="abs contact-row" style="left:366px;top:4102px">
  <i><svg viewBox="0 0 16 16"><path fill="#6e1f2c" d="M8 1a5 5 0 0 0-5 5c0 4 5 9 5 9s5-5 5-9a5 5 0 0 0-5-5zm0 7a2 2 0 1 1 0-4 2 2 0 0 1 0 4z"/></svg></i>
  <span>Larkfield Business park,<br>Holmshire</span></div>
<div class="abs contact-row" style="left:366px;top:4186px">
  <i><svg viewBox="0 0 16 16" fill="none" stroke="#6e1f2c" stroke-width="1.5"><rect x="2" y="3.5" width="12" height="9"/><path d="M2 4l6 5 6-5"/></svg></i>
  <span>www.brenvashine.co.uk</span></div>
<div class="abs contact-row" style="left:366px;top:4240px">
  <i><svg viewBox="0 0 16 16"><path fill="#6e1f2c" d="M4 1.5l2.5 3-1.5 1.5c.8 2 2.5 3.7 4.5 4.5L11 9l3 2.5-1.5 2.5C7 14 2 9 2 3z"/></svg></i>
  <span>07700 900418</span></div>
<div class="abs map" role="img" aria-label="Map showing the bodyshop location"></div>
<div class="abs directions"><svg viewBox="0 0 16 16" width="14" height="14"><path fill="#222" d="M9 2l6 5-6 5V9C5 9 3 10 1 13c0-5 3-7 8-7.5z"/></svg>GET DIRECTIONS</div>
<svg class="abs" style="left:952px;top:4170px" width="16" height="22" viewBox="0 0 16 22"><path fill="#d0021b" d="M8 0a8 8 0 0 0-8 8c0 6 8 14 8 14s8-8 8-14a8 8 0 0 0-8-8z"/><circle cx="8" cy="8" r="3" fill="#fff"/></svg>
<div class="abs foot-rule"></div>
<div class="abs social"><i></i><i></i><i></i></div>
<p class="abs center copy">© 2019 Brenvashine. All Rights Reserved</p>
<p class="abs pay">TILLWAVE</p>

</body>
</html>
```